TK Homes - Stone Dorf Design

Looking for a double sides design, 1 side for my realestate and the other for home building. ( TK Homes on 1 side, Stone Dorf card on the other Side
Side 1 - Marek Tove ~ Vox Realty logo and Company ( the Property quarter )
Marek Tove
Marek@Marektove.example
IG - Marek_Bzq_Realtor
FB - marekt
Cell - 5558130467
3847 61 St Nw

Side 2
Marek Tove
5558130467
IG - Stonedorf_Bzq
Stonedorfdev@mailbox.example

Target Market(s)

Home buyers/ sellers

Industry/Entity Type

Home builders - Realestate

Contact Information for Business Card

Above

Requirements
Must have
• Black OR White background - my information -

```html
<!DOCTYPE html>
<html lang="en">
<head>
<meta charset="utf-8">
<title>TK Homes – Stone Dorf Design business cards</title>
<link rel="stylesheet" href="https://fonts.googleapis.com/css2?family=Cinzel:wght@500;600&family=Tinos&display=swap">
<style>
  :root {
    --page-bg: #161616;
    --card-bg: #232323;
    --ink: #f2f2f2;
    --accent: #1b7cca;
    --muted: #9a9a9a;
    --badge: #3a3a3a;
  }
  * { box-sizing: border-box; margin: 0; padding: 0; }
  html, body { width: 1200px; height: 1059px; overflow: hidden; background: var(--page-bg); }
  .canvas { position: relative; width: 1200px; height: 1059px; }
  .card {
    position: absolute; left: 256px; width: 690px; height: 392px;
    background: var(--card-bg); border-radius: 18px;
    box-shadow: 0 10px 24px rgba(0,0,0,.55);
    color: var(--ink);
  }
  .card--realty { top: 89px; }
  .card--builder { top: 547px; }

  .brand-mark {
    position: absolute; left: 0; right: 0; text-align: center;
    font-family: "Cinzel", serif; font-weight: 600;
  }
  .card--realty .brand-mark { top: 70px; font-size: 62px; color: var(--accent); letter-spacing: 2px; }
  .brand-name--tagline { position: absolute; left: 0; right: 0; top: 156px; text-align: center;
    font-family: "Cinzel", serif; font-weight: 600; font-size: 40px; color: var(--ink); }

  .card--builder .brand-mark { top: 124px; font-size: 50px; color: var(--ink); letter-spacing: 1px; line-height: 1; }
  .card--builder .brand-sub { top: 180px; font-size: 16px; letter-spacing: 6px; line-height: 1; }

  .divider { position: absolute; left: 343px; width: 1.5px; background: var(--accent); }
  .card--realty .divider { top: 240px; height: 96px; }
  .card--builder .divider { top: 238px; height: 101px; }

  .person {
    position: absolute; right: calc(690px - 320px); text-align: right;
    font-family: "Cinzel", serif; font-weight: 500; white-space: nowrap;
  }
  .card--realty .person { top: 243px; font-size: 27px; }
  .card--builder .person { top: 266px; font-size: 34px; }

  .social { position: absolute; right: 370px; font-family: "Tinos", serif; font-size: 17px;
    display: flex; align-items: center; gap: 7px; white-space: nowrap; }
  .social .dot { width: 11px; height: 11px; background: var(--accent); }
  .social .dot--round { border-radius: 50%; }

  .contacts { position: absolute; list-style: none; font-family: "Tinos", serif; }
  .contacts li { display: flex; align-items: center; white-space: nowrap; }
  .contacts svg { width: 14px; height: 14px; margin-right: 9px; flex: none; fill: var(--accent); }
  .card--realty .contacts { left: 366px; top: 234px; font-size: 18px; }
  .card--realty .contacts li { height: 26.5px; }
  .card--builder .contacts { left: 373px; top: 231px; font-size: 19px; }
  .card--builder .contacts li { height: 29.5px; }
  .contacts .dot { width: 13px; height: 13px; margin-right: 10px; background: var(--accent); border-radius: 3px; flex: none; }

  .partner-badge { position: absolute; top: 338px; height: 27px; background: var(--badge); border-radius: 3px; }
  .partner-badge--district { left: 539px; width: 71px; }
  .partner-badge--realty { left: 621px; width: 42px; border-radius: 50%/40%; }
</style>
</head>
<body>
<main class="canvas">

  <section class="card card--realty" aria-label="Real estate side">
    <div class="brand-mark">TK Homes</div>
    <div class="brand-name--tagline">Marek Tove</div>

    <div class="person">Marek Tove</div>
    <div class="social" style="top:287px">Marek_Bzq_Realtor <span class="dot"></span></div>
    <div class="social" style="top:312px">marekt <span class="dot dot--round"></span></div>

    <div class="divider"></div>

    <ul class="contacts">
      <li><svg viewBox="0 0 24 24"><path d="M6.6 10.8a15 15 0 0 0 6.6 6.6l2.2-2.2a1 1 0 0 1 1-.25 11.4 11.4 0 0 0 3.6.57 1 1 0 0 1 1 1V20a1 1 0 0 1-1 1A17 17 0 0 1 3 4a1 1 0 0 1 1-1h3.5a1 1 0 0 1 1 1c0 1.25.2 2.45.57 3.6a1 1 0 0 1-.25 1z"/></svg>5558130467</li>
      <li><svg viewBox="0 0 24 24"><path d="M2 9l10-7 10 7v12H2zM4 10l8 6 8-6-8-5.5z"/></svg>Marek@Marektove.example</li>
      <li><svg viewBox="0 0 24 24"><circle cx="12" cy="12" r="10"/></svg>www.Marektove.example</li>
      <li><svg viewBox="0 0 24 24"><path d="M12 2a7 7 0 0 0-7 7c0 5 7 13 7 13s7-8 7-13a7 7 0 0 0-7-7zm0 9.5A2.5 2.5 0 1 1 12 6.5a2.5 2.5 0 0 1 0 5z"/></svg>3847 61 St Nw</li>
    </ul>

    <div class="partner-badge partner-badge--district" role="img" aria-label="The Property quarter partner badge"></div>
    <div class="partner-badge partner-badge--realty" role="img" aria-label="Vox Realty partner badge"></div>
  </section>

  <section class="card card--builder" aria-label="Home building side">
    <div class="brand-mark">Stone Dorf</div>
    <div class="brand-mark brand-sub">DEVELOPMENTS</div>

    <div class="person">Marek Tove</div>

    <div class="divider"></div>

    <ul class="contacts">
      <li><svg viewBox="0 0 24 24"><path d="M6.6 10.8a15 15 0 0 0 6.6 6.6l2.2-2.2a1 1 0 0 1 1-.25 11.4 11.4 0 0 0 3.6.57 1 1 0 0 1 1 1V20a1 1 0 0 1-1 1A17 17 0 0 1 3 4a1 1 0 0 1 1-1h3.5a1 1 0 0 1 1 1c0 1.25.2 2.45.57 3.6a1 1 0 0 1-.25 1z"/></svg>5558130467</li>
      <li><svg viewBox="0 0 24 24"><path d="M2 9l10-7 10 7v12H2zM4 10l8 6 8-6-8-5.5z"/></svg>Stonedorfdev@mailbox.example</li>
      <li><svg viewBox="0 0 24 24"><circle cx="12" cy="12" r="10"/></svg>www.stonedorfdev.example</li>
      <li><span class="dot"></span>Stonedorf_Bzq</li>
    </ul>
  </section>

</main>
</body>
</html>
```